Bold Harbor Web Design Layout (no HTML)

We require the layout only for a website.  No html or logo is required - just the layout.

A refreshed and revitalized website to coincide with the relaunch of our brand. We are looking for a clean simplistic design that is easy to use and presents relevant information effectively.
We are an events management company specializing in conferences.
Updates

Thank you for your design. We really like the imagery. Essentially we are after a home page design (one page) that incorporates the 3 main buttons (request a proposal, select a venue and specials) while providing the relevant information on our service via functionality similar to that on www.plivtrak.com ie using the large arrow to scroll over the relevant topic to receive information. We hope to finalise the contest in the next week and hope to consider your revised entry.

Thanks!

Target Market(s)

Australian corporate sector primarily Managing Directors or their assistants. Any business looking to hold a conference for up 500 delegates however we are primarily targeting the decision maker so need to ensure we are communicating on their terms.

Industry/Entity Type

Event

Requirements
Must have
• Incorporate the elements from the attached document however with complete creative license as to their layout. Our main competitors are gathorly.com.au, talkhollowhq.com.au both sites are bland and not user friendly.
Nice to have
• Colours red, silver and black. Note we are running a separate contest to refresh our logo.
• We like the functionality of plivtrak.com

```html
<!DOCTYPE html>
<html lang="en">
<head>
<meta charset="utf-8">
<title>Bold Harbor – Conference Management</title>
<link href="https://fonts.googleapis.com/css2?family=Questrial&family=Arimo:wght@400;700&display=swap" rel="stylesheet">
<style>
:root{
  --black:#000;
  --white:#fff;
  --red:#e00000;
  --red-dark:#b80000;
  --grey-panel:#e6e6e6;
  --grey-text:#858585;
  --grey-head:#666;
  --tab-dark:#3a3a3a;
  --ink:#111;
}
*{box-sizing:border-box;margin:0;padding:0}
html,body{width:1200px;height:740px;overflow:hidden}
body{
  position:relative;
  background:linear-gradient(var(--black) 0 107px,var(--white) 107px 152px,var(--black) 152px);
  font-family:"Questrial",sans-serif;color:var(--ink);
}
.sheet{position:absolute;left:102px;top:9px;width:978px;height:690px;background:var(--white);border-radius:10px}
.masthead{
  position:absolute;left:111px;top:16px;width:958px;height:92px;border-radius:8px 8px 0 0;overflow:hidden;
  background:
    radial-gradient(ellipse 260px 60px at 390px 40px,rgba(255,140,0,.55),transparent 70%),
    radial-gradient(ellipse 180px 80px at 880px 60px,rgba(200,200,200,.8),transparent 70%),
    linear-gradient(90deg,#050505 0 110px,#d90000 220px,#ff2a00 380px,#ff8a00 530px,#e01000 640px,#8a8a8a 860px,#c8c8c8 958px);
}
.logo-text{position:absolute;left:43px;top:49px;font-family:"Arimo",sans-serif;font-size:11px;color:var(--white)}
.search{position:absolute;left:651px;top:54px;display:flex;align-items:center;gap:4px}
.search label{font-family:"Arimo",sans-serif;font-weight:700;font-size:14px;color:#111}
.search .field{width:198px;height:22px;background:var(--white);border:1px solid #999}
.search .go{width:30px;height:30px;border-radius:4px;background:var(--red);border:1px solid #fff;color:var(--white);font-family:"Arimo",sans-serif;font-weight:700;font-size:13px;display:flex;align-items:center;justify-content:center}
.main-nav{position:absolute;left:111px;top:108px;width:958px;height:44px;background:var(--black);display:flex;gap:14px;padding-left:78px;align-items:center;padding-top:10px}
.main-nav a{color:var(--white);text-decoration:none;font-size:15px}
.main-nav a.current{font-weight:700;color:#dfe8f4;position:relative}
.main-nav a.current::after{content:"";position:absolute;left:50%;bottom:-12px;margin-left:-6px;border:6px solid transparent;border-bottom-color:var(--white)}
.side-menu{position:absolute;left:111px;top:214px;list-style:none}
.side-menu li{height:31px;line-height:31px;padding-left:21px;font-size:15.5px;color:#111}
.side-menu li.active{width:148px;height:34px;line-height:34px;color:var(--white);background:linear-gradient(var(--red),var(--red-dark));clip-path:polygon(0 0,134px 0,100% 50%,134px 100%,0 100%);border-radius:4px 0 0 4px;margin-bottom:0}
.divider{position:absolute;width:2px;background:linear-gradient(transparent,#ddd 10%,#ddd 90%,transparent)}
.intro{position:absolute;left:291px;top:175px;width:535px;font-size:18px;line-height:21px}
.intro b{font-family:"Arimo",sans-serif}
.finance{position:absolute;left:274px;top:264px;width:549px;height:264px;background:var(--grey-panel);border-radius:8px}
.finance h2{position:absolute;left:0;right:0;top:12px;text-align:center;font-family:"Arimo",sans-serif;font-size:16px;color:var(--grey-head)}
.finance .art{position:absolute;left:46px;top:61px;width:110px;height:155px;border-radius:40px 40px 30px 30px;background:radial-gradient(circle at 45% 40%,#ff3a2a,#b30000 70%)}
.finance ul{position:absolute;left:166px;top:48px;list-style:none;font-size:14.5px;line-height:17.5px;color:var(--grey-text)}
.finance li::before{content:"•";margin-right:8px}
.finance p{position:absolute;left:165px;top:188px;width:360px;font-size:14.5px;line-height:17.5px;color:var(--grey-text)}
.goals{position:absolute;left:832px;top:170px;width:225px;height:361px;border-radius:8px;background:linear-gradient(var(--red),var(--red-dark));color:var(--white)}
.goals .lead{position:absolute;left:7px;top:36px;font-size:19px;line-height:23px}
.goals .item{position:absolute;left:13px;font-size:21px;line-height:24px}
.pointer{position:absolute;left:772px;top:290px;width:279px;height:66px}
.pointer span{position:absolute;left:73px;top:18px;font-size:21px;color:var(--white)}
.card{position:absolute;top:545px;width:222px;font-family:"Arimo",sans-serif}
.card h3{height:21px;line-height:21px;padding-left:9px;font-weight:400;font-size:13px;color:var(--white);background:var(--red);border-radius:0 6px 6px 0}
.card p{width:118px;margin:1px 0 0 5px;font-size:11.5px;line-height:13.5px;color:#111}
.card .art{position:absolute;top:26px}
.badge{left:144px;width:78px;height:78px;border-radius:50%;background:radial-gradient(circle,#ff3a1a,#c40000)}
.clock{left:149px;width:78px;height:78px;border-radius:50%;background:radial-gradient(circle,#fff 55%,#d6d6d6 62%,#b00 66%,#e8e8e8 72%)}
.map{left:127px;top:28px!important;width:82px;height:84px;border-radius:40% 50% 45% 35%;background:linear-gradient(#ff4a2a,#c00000)}
.site-footer{position:absolute;left:111px;top:663px;width:958px;height:27px;background:var(--black);color:var(--white);font-family:"Arimo",sans-serif;font-size:10px;text-align:center;line-height:27px}
</style>
</head>
<body>
<div class="sheet"></div>

<header class="masthead">
  <div class="logo-text">LOGO GOES HERE</div>
  <div class="search"><label>SEARCH:</label><div class="field"></div><div class="go">GO</div></div>
</header>

<nav class="main-nav">
  <a class="current">HOME</a><a>SERVICES</a><a>VENUES</a><a>CLIENTS</a><a>REGISTER</a><a>CONTACT US</a>
</nav>

<ul class="side-menu">
  <li class="active">OTHER MENU</li>
  <li>OTHER MENU</li><li>OTHER MENU</li><li>OTHER MENU</li><li>OTHER MENU</li><li>OTHER MENU</li>
</ul>

<div class="divider" style="left:260px;top:175px;height:475px"></div>

<p class="intro"><b>Bold Harbor</b>’ professional conference team specialises in solutions. We work closely with a core group of clients to ensure desired outcomes, on time and in budget.</p>

<section class="finance">
  <h2>We offer a complete range of finance&nbsp; packages including;</h2>
  <div class="art" role="img" aria-label="Red glossy dollar sign illustration"></div>
  <ul>
    <li>total conference underwriting</li>
    <li>online delegate payment gateway</li>
    <li>substantially discounted rooming rates</li>
    <li>no upfront costs</li>
    <li>zero management fees</li>
    <li>free venue sourcing</li>
    <li>free delegate booking management</li>
  </ul>
  <p>Minimise your costs and free your cash flow to focus on your core business functions. We’ll ensure maximum return from your conference budget.</p>
</section>

<aside class="goals">
  <p class="lead">Our goal is to make<br>sure your conference is:</p>
  <p class="item" style="top:184px">Expertely Managed<br>&amp; Hassle Free</p>
  <p class="item" style="top:248px">Outcome Focussed</p>
  <p class="item" style="top:293px">Well Attended</p>
</aside>

<div class="pointer">
  <svg width="279" height="66" viewBox="0 0 279 66">
    <path d="M2 33 L34 3 H272 Q277 3 277 8 V58 Q277 63 272 63 H34 Z" fill="var(--white)"/>
    <path d="M8 33 L36 7 H269 Q273 7 273 11 V55 Q273 59 269 59 H36 Z" fill="var(--tab-dark)"/>
  </svg>
  <span>Cost Effective</span>
</div>

<div class="card" style="left:274px">
  <h3>Special Offers</h3>
  <p>Not sure where to start? We have over 60 properties to choose from both domestically and international.</p>
  <div class="art badge" role="img" aria-label="Red starburst badge with dollar sign"></div>
</div>
<div class="divider" style="left:525px;top:540px;height:115px"></div>
<div class="card" style="left:551px">
  <h3>Request Proposal</h3>
  <p>Not sure where to start? We have over 60 properties to choose from both domestically and international.</p>
  <div class="art clock" role="img" aria-label="Wall clock illustration"></div>
</div>
<div class="divider" style="left:818px;top:540px;height:115px"></div>
<div class="card" style="left:836px">
  <h3>Browse Conference</h3>
  <p>Not sure where to start? We have over 60 properties to choose from both domestically and international.</p>
  <div class="art map" role="img" aria-label="Red map of Australia"></div>
</div>

<footer class="site-footer">Ph: 1300 555 274. P.O. Box 4471, Harbourside NSW 2099. Bold Harbor. All Rights Reserved. 2009</footer>
</body>
</html>
```